Social Media Cover and Profile

We already have our own logo. We just need a fresh design on our social media pages. We are not happy with our current designs. We would like to incorporate our ZING billboard and the colors are blue (#05143f) and white. You can also incorporate silver as well. We are a family law office (Divorce and Custody) We no longer want to incorporate the Capital of Harrisburg photo that we are currently using. You can look at our Facebook page; The Law Office of Milo T. Brennick.

Target Market(s)

Potential Clients

Industry/Entity Type

Family Law

Logo Text

Our Logo Is The Law Office of Milo T. Brennick with the Sheild

Requirements
Must have
• Text to include:
Central Pennslyvania's Premier Family Law Firm

Ability to be resized to and used as all images in social media, including but not limited to: Youtube Channel art, Facebook Cover and Profile.
Nice to have
• Darker color but we are open to "bright" ideas.

```html
<!DOCTYPE html>
<html lang="en">
<head>
<meta charset="UTF-8">
<title>ZING – Social Media Cover</title>
<link href="https://fonts.googleapis.com/css2?family=Archivo:wght@700&family=Playfair+Display:wght@600&display=swap" rel="stylesheet">
<style>
  :root {
    --page-bg: #f2f2f2;
    --navy: #05143f;
    --navy-deep: #020a2c;
    --navy-side: #0b1f58;
    --silver-light: #e4e4e6;
    --silver-mid: #a9a9ad;
    --silver-dark: #8b8b90;
    --tagline: #d9d9dc;
  }
  * { margin: 0; padding: 0; box-sizing: border-box; }
  html, body {
    width: 1200px;
    height: 720px;
    overflow: hidden;
    background: var(--page-bg);
  }
  .cover {
    position: absolute;
    left: 50px;
    top: 154px;
    width: 1100px;
    height: 420px;
    background: radial-gradient(ellipse at 50% 40%, var(--navy) 0%, var(--navy-deep) 100%);
    box-shadow: 0 10px 14px rgba(0, 0, 0, 0.35);
    overflow: hidden;
  }
  .side-decoration {
    position: absolute;
    top: 0;
    bottom: 0;
    width: 200px;
  }
  .side-decoration--left {
    left: 0;
    background: linear-gradient(90deg, var(--navy-side) 0%, rgba(11, 31, 88, 0) 100%);
  }
  .side-decoration--right {
    right: 0;
    background: linear-gradient(270deg, var(--navy-side) 0%, rgba(11, 31, 88, 0) 100%);
  }
  .campaign-word {
    position: absolute;
    left: 0;
    right: 0;
    top: 78px;
    text-align: center;
    font-family: "Archivo", Arial, sans-serif;
    font-weight: 700;
    font-size: 250px;
    line-height: 1;
    letter-spacing: 4px;
    background: linear-gradient(180deg, var(--silver-light) 0%, var(--silver-mid) 45%, var(--silver-dark) 55%, var(--silver-light) 100%);
    -webkit-background-clip: text;
    background-clip: text;
    color: transparent;
  }
  .tagline {
    position: absolute;
    left: 0;
    right: 0;
    top: 303px;
    text-align: center;
    font-family: "Playfair Display", Georgia, serif;
    font-weight: 600;
    font-size: 32px;
    color: var(--tagline);
    letter-spacing: 0.3px;
  }
</style>
</head>
<body>
  <section class="cover">
    <div class="side-decoration side-decoration--left" role="img" aria-label="Decorative navy wave pattern with thin silver curves"></div>
    <div class="side-decoration side-decoration--right" role="img" aria-label="Decorative navy wave pattern with thin silver curves"></div>
    <h1 class="campaign-word">ZING</h1>
    <p class="tagline">Central Pennslyvania's Premier Family Law Firm</p>
  </section>
</body>
</html>
```